Ward Compass Business Card Design*

We need a business card design for our company Ward Compass. Our company is specialized in providing online consulting services regarding medical institutions, hospitals and doctors. We work with patients worldwide looking to choose between healthcare providers. We have a website you may use as a reference, where we list doctors and clinics worldwide. So we target Medical providers as well as patients worldwide.
Target Market(s)
Medical Providers and patients around the world
Industry/Entity Type
Medical
Contact Information for Business Card
Salwa Kettani
CEO
+90 612 348 2175
info@wardcompass.example
www.wardcompass.example
14 Annakhil 7 H.R.B. Rabat, Morocco
Requirements
Must have
- Company logo/name on one full side, personal info and smaller logo and company name on the other side.
Nice to have
- Smart and elegant design

```html
<!DOCTYPE html>
<html lang="en">
<head>
<meta charset="utf-8">
<title>Ward Compass – Business Card</title>
<link href="https://fonts.googleapis.com/css2?family=Montserrat:wght@400;500;700&display=swap" rel="stylesheet">
<style>
  :root {
    --navy: #14386a;
    --grey: #8a8a8a;
    --paper: #ffffff;
    --backdrop: #d2d1cd;
  }
  * { margin: 0; padding: 0; box-sizing: border-box; }
  html, body {
    width: 1200px; height: 801px; overflow: hidden;
    background: var(--backdrop);
    font-family: "Montserrat", Arial, sans-serif;
  }
  .sheet {
    position: relative; width: 1200px; height: 801px;
    display: flex; align-items: center; justify-content: center; gap: 50px;
  }
  .card {
    position: relative; width: 540px; height: 308px;
    box-shadow: 0 8px 22px rgba(0,0,0,0.22);
    overflow: hidden;
  }
  /* front */
  .card--front { background: var(--paper); }
  .front-band {
    position: absolute; left: 0; top: 56px; width: 300px; height: 64px;
    background: var(--navy);
  }
  .holder-name {
    position: absolute; left: 28px; top: 12px;
    color: var(--paper); font-weight: 700; font-size: 16px; letter-spacing: 0.5px;
  }
  .holder-role {
    position: absolute; left: 48px; top: 36px;
    color: var(--paper); font-weight: 500; font-size: 13px; letter-spacing: 0.5px;
  }
  .front-mark {
    position: absolute; left: 266px; top: 54px; width: 68px; height: 68px;
    border-radius: 50%; border: 10px solid var(--navy); background: var(--paper);
  }
  .front-brand {
    position: absolute; left: 346px; top: 72px;
    color: var(--navy); font-weight: 700; font-size: 20px; letter-spacing: 1px;
    text-transform: uppercase;
  }
  .address {
    position: absolute; left: 150px; top: 160px;
    color: var(--grey); font-size: 11.5px; line-height: 16px;
  }
  .contacts {
    position: absolute; left: 150px; top: 214px; list-style: none;
    color: var(--grey); font-size: 11.5px;
  }
  .contacts li { display: flex; align-items: center; gap: 8px; height: 20px; }
  .contacts svg { width: 12px; height: 12px; fill: var(--navy); flex: none; }
  /* back */
  .card--back {
    background: var(--navy);
    display: flex; align-items: center; justify-content: center; gap: 18px;
  }
  .back-mark {
    width: 74px; height: 74px; border-radius: 50%;
    border: 10px solid var(--paper);
  }
  .back-brand {
    color: var(--paper); font-weight: 700; font-size: 26px; letter-spacing: 1.5px;
    text-transform: uppercase;
  }
</style>
</head>
<body>
<main class="sheet">
  <section class="card card--front" aria-label="Card front">
    <div class="front-band">
      <p class="holder-name">SALWA KETTANI</p>
      <p class="holder-role">CEO</p>
    </div>
    <div class="front-mark" aria-hidden="true"></div>
    <p class="front-brand">Ward Compass</p>
    <p class="address">14 Annakhil 7 H.R.B.<br>Rabat, Morocco</p>
    <ul class="contacts">
      <li>
        <svg viewBox="0 0 24 24" aria-hidden="true"><path d="M6.6 10.8a15.1 15.1 0 0 0 6.6 6.6l2.2-2.2c.3-.3.7-.4 1-.2 1.1.4 2.3.6 3.6.6.6 0 1 .4 1 1V20c0 .6-.4 1-1 1A17 17 0 0 1 3 4c0-.6.4-1 1-1h3.5c.6 0 1 .4 1 1 0 1.3.2 2.5.6 3.6.1.3 0 .7-.2 1z"/></svg>
        +90 612 348 2175
      </li>
      <li>
        <svg viewBox="0 0 24 24" aria-hidden="true"><path d="M2 5h20v14H2zm2 2v.5l8 5 8-5V7zm0 2.8V17h16V9.8l-8 5z"/></svg>
        info@wardcompass.example
      </li>
      <li>
        <svg viewBox="0 0 24 24" aria-hidden="true"><path d="M12 2a10 10 0 1 0 0 20 10 10 0 0 0 0-20zm-1 17.9A8 8 0 0 1 4.1 11H7c.1 3.3 1.5 6.5 4 8.9zm0-10.9H9c.1-2.5 1-4.9 2-6.9zm2 10.9c2.5-2.4 3.9-5.6 4-8.9h2.9a8 8 0 0 1-6.9 8.9zM15 9h-2V2.1c1 2 1.9 4.4 2 6.9z"/></svg>
        www.wardcompass.example
      </li>
    </ul>
  </section>

  <section class="card card--back" aria-label="Card back">
    <div class="back-mark" aria-hidden="true"></div>
    <p class="back-brand">Ward Compass</p>
  </section>
</main>
</body>
</html>
```